Website for a Pittsburgh Musical Production

We are creating a website for a musical stage production. Content and copy is included below. We are targeting production in early 2023.

```html
<!DOCTYPE html>
<html lang="en">
<head>
<meta charset="utf-8">
<title>Creation The Rock Opera</title>
<link rel="stylesheet" href="https://fonts.googleapis.com/css2?family=Jura:wght@400;500;600&family=Play:wght@400;700&display=swap">
<style>
:root{
  --ink:#ffffff;
  --text:#e6e6e6;
  --muted:#bdbdbd;
  --green:#6fa85a;
  --green-btn:#6aa257;
  --page:#0c0c0d;
  --welcome:#1b1b1d;
  --about:#19191b;
  --footer:#0e0e10;
  --frame:#4a4a4c;
}
*{box-sizing:border-box;margin:0;padding:0}
html,body{width:1200px;height:3350px;overflow:hidden;background:var(--page)}
body{font-family:"Jura",sans-serif;color:var(--text)}
.page{position:relative;width:1200px;height:3350px;overflow:hidden;background:var(--page)}
.abs{position:absolute}
.heading{font-family:"Play",sans-serif;font-weight:400;color:var(--ink);letter-spacing:2px;text-align:center;left:0;width:1200px}
.btn{position:absolute;display:flex;align-items:center;justify-content:center;font-family:"Play",sans-serif;font-size:18px;letter-spacing:.5px;color:var(--ink);border-radius:30px;text-decoration:none}

/* welcome band sits behind the slanted hero edge */
.welcome{left:0;top:560px;width:1200px;height:524px;background:var(--welcome)}

/* hero */
.hero{left:0;top:0;width:1200px;height:672px;background:
  radial-gradient(ellipse at 62% 20%,#3b3b3b 0%,#1c1c1c 35%,#0a0a0a 75%),#0a0a0a;
  clip-path:polygon(0 0,100% 0,100% 628px,0 672px)}
.brand{left:143px;top:12px;font-family:"Play",sans-serif;font-size:40px;font-weight:400;color:var(--green);letter-spacing:.5px}
.nav{left:408px;top:42px;display:flex;font-family:"Jura",sans-serif;font-size:12px;font-weight:600;letter-spacing:.5px}
.nav a{color:var(--ink);text-decoration:none;margin-right:23px;position:relative;padding-bottom:10px}
.nav a.active{color:var(--green)}
.nav a.active::after{content:"";position:absolute;left:0;right:0;bottom:0;height:1px;background:var(--green)}
.hero-title{top:242px;font-size:49px;letter-spacing:3px}
.hero-sub{left:0;width:1200px;top:306px;text-align:center;font-size:15px;letter-spacing:11px;color:var(--text)}
.btn-trailer{left:516px;top:355px;width:170px;height:48px;background:var(--green-btn);border:2px solid #cfe3c5}
.dots{left:580px;top:611px;display:flex;gap:9px}
.dots span{width:8px;height:8px;border-radius:50%;background:#fff}
.dots span.off{background:none;border:1px solid #fff}

.welcome-title{top:734px;font-size:39px;color:var(--green);letter-spacing:2px}
.copy{left:215px;width:770px;text-align:center;font-size:14px;line-height:22px;color:var(--text);letter-spacing:.7px}
.btn-read{left:516px;top:958px;width:169px;height:51px;border:2px solid #cfcfcf;background:none}

/* media */
.media{left:0;top:1084px;width:1200px;height:958px;background:linear-gradient(180deg,#1a1a1c 0%,#101010 40%,#080808 100%)}
.media-title{top:1134px;font-size:35px}
.media-sub{left:0;width:1200px;top:1190px;text-align:center;font-size:14px;letter-spacing:.6px}
.shot{width:289px;height:296px}
.btn-more{left:514px;top:1913px;width:172px;height:52px;background:#1c1c1e}

/* about */
.about{left:0;top:2042px;width:1200px;height:612px;background:var(--about)}
.about-title{top:2093px;font-size:35px}
.about-text{left:143px;top:2212px;width:340px;font-size:16px;line-height:28px;letter-spacing:1.1px;color:var(--text)}
.btn-learn{left:143px;top:2506px;width:163px;height:48px;background:var(--green-btn)}
.portrait{left:524px;top:2189px;width:533px;height:393px;border:5px solid var(--frame);background:radial-gradient(ellipse at 55% 40%,#6a6a6a 0%,#2b2b2b 40%,#0c0c0c 80%)}

/* video */
.video{left:0;top:2654px;width:1200px;height:420px;background:
  radial-gradient(ellipse at 72% 45%,#5a2a24 0%,#3a1414 30%,transparent 65%),
  radial-gradient(ellipse at 15% 75%,#3e1e18 0%,transparent 40%),
  linear-gradient(180deg,#2a0e10 0%,#3c0f12 55%,#1f0a0b 100%)}
.video-title{top:2740px;font-size:35px}
.video-text{left:200px;width:800px;top:2803px;text-align:center;font-size:12px;line-height:15px;letter-spacing:.4px;color:var(--text)}
.play{left:563px;top:2856px}

/* footer */
.footer{left:0;top:3074px;width:1200px;height:276px;background:var(--footer)}
.foot-head{font-size:14px;color:var(--green);letter-spacing:.5px;top:3115px;font-weight:400}
.foot-list{list-style:none;font-size:12px;line-height:24px;letter-spacing:.6px;color:var(--text);top:3144px}
.foot-contact{left:559px;top:3144px;font-size:12px;line-height:24px;color:var(--text)}
.foot-contact .wide{letter-spacing:5px}
.foot-contact .norm{letter-spacing:.8px}
.mail{left:798px;font-size:12px;letter-spacing:.6px;color:var(--text);display:flex;align-items:center;gap:5px}
.rule{left:143px;top:3296px;width:914px;height:1px;background:#2a2a2c}
.copyright{left:143px;top:3310px;font-size:10px;letter-spacing:.4px;color:var(--muted)}
.legal{left:900px;top:3311px;font-size:9px;color:#555;letter-spacing:.4px}
</style>
</head>
<body>
<div class="page">

  <div class="abs welcome"></div>

  <div class="abs hero" role="img" aria-label="Dim backstage film set with crew silhouettes, lights and camera rigs"></div>
  <div class="abs brand">Creation</div>
  <nav class="abs nav">
    <a class="active">HOME</a><a>NEWS</a><a>STORY</a><a>MUSIC</a><a>MEDIA</a><a>COMPOSERS</a><a>PRODUCTIONS</a><a>MERCHANDISE</a><a>CONTACT</a>
  </nav>
  <h1 class="abs heading hero-title">CREATION THE ROCK OPERA</h1>
  <p class="abs hero-sub">We are a new Creation The Rock Opera</p>
  <a class="btn btn-trailer">VIEW TRAILER</a>
  <div class="abs dots"><span class="off"></span><span></span><span></span></div>

  <h2 class="abs heading welcome-title">WELCOME TO CREATION</h2>
  <p class="abs copy" style="top:795px">Lorem ipsum dolor sit amet, consectetur adipiscing elit, sed do eiusmod tempor incididunt ut labore et dolore magna aliqua. Ut enim ad minim veniam, quis nostrud exercitation ullamco laboris nisi ut aliquip ex ea commodo consequat.</p>
  <p class="abs copy" style="top:875px">Neque porro quisquam est, qui dolorem ipsum quia dolor sit amet, consectetur, adipisci velit, sed quia non numquam eius modi tempora incidunt ut labore et dolore magnam aliquam quaerat voluptatem.</p>
  <a class="btn btn-read">READ MORE</a>

  <div class="abs media"></div>
  <h2 class="abs heading media-title">CREATION MEDIA</h2>
  <p class="abs media-sub">Excepteur sint occaecat cupidatat non proident, sunt in culpa qui officia deserunt mollit anim id est laborum</p>
  <div class="abs shot" style="left:143px;top:1248px;background:radial-gradient(ellipse at 70% 45%,#3d4a2a,#0f2410 70%)" role="img" aria-label="Singer with microphone under green stage light"></div>
  <div class="abs shot" style="left:455px;top:1248px;background:radial-gradient(ellipse at 55% 45%,#3a2a5c,#140f26 75%)" role="img" aria-label="Two performers on a purple lit stage"></div>
  <div class="abs shot" style="left:767px;top:1248px;background:radial-gradient(ellipse at 50% 55%,#6a6a70,#1a1a1c 70%)" role="img" aria-label="Costumed performer surrounded by sparks"></div>
  <div class="abs shot" style="left:143px;top:1567px;background:radial-gradient(ellipse at 55% 40%,#4d6a8c,#0f1a2c 75%)" role="img" aria-label="Performer in stage makeup under blue light"></div>
  <div class="abs shot" style="left:455px;top:1567px;background:radial-gradient(ellipse at 50% 35%,#8a4a24,#2a140c 75%)" role="img" aria-label="Fire performers on stage"></div>
  <div class="abs shot" style="left:767px;top:1567px;background:radial-gradient(ellipse at 50% 50%,#5a4a3a,#140e0c 75%)" role="img" aria-label="Performer playing guitar in jacket"></div>
  <a class="btn btn-more">VIEW MORE</a>

  <div class="abs about"></div>
  <h2 class="abs heading about-title">ABOUT CREATION</h2>
  <p class="abs about-text">Like Ada Merriwell’s classic tale, our story begins on the frigid seas of the Arctic Circle, where mountains of ice block Captain Harlow and his crew on their voyage to the North Pole. Ignoring the imminent mutiny of his sailors, Captain Harlow has locked himself in his cabin and tends to a dying stranger whom he recently dragged aboard.</p>
  <a class="btn btn-learn">LEARN MORE</a>
  <div class="abs portrait" role="img" aria-label="Black and white photo of the captain character in a top hat"></div>

  <div class="abs video" role="img" aria-label="Stage scene with performers under red light"></div>
  <h2 class="abs heading video-title">CREATION VIDEO</h2>
  <p class="abs video-text">Temporibus autem quibusdam et aut officiis debitis aut rerum necessitatibus saepe eveniet ut et voluptates repudiandae sint et molestiae non recusandae.</p>
  <svg class="abs play" width="74" height="74" viewBox="0 0 74 74" aria-label="Play video">
    <circle cx="37" cy="37" r="35" fill="#0a0a0a" stroke="#fff" stroke-width="2.5"/>
    <path d="M29 22 L53 37 L29 52 Z" fill="#fff"/>
  </svg>

  <div class="abs footer"></div>
  <h3 class="abs foot-head" style="left:143px">Navigation</h3>
  <ul class="abs foot-list" style="left:143px"><li>News</li><li>Story</li><li>Music</li><li>Media</li><li>Composers</li></ul>
  <ul class="abs foot-list" style="left:335px"><li>Productions</li><li>Merchandise</li><li>Contact</li></ul>
  <h3 class="abs foot-head" style="left:559px">Contact Info</h3>
  <div class="abs foot-contact">
    <div class="wide">Dana Whitlock</div>
    <div class="wide">Media Director</div>
    <div class="norm">Creation The Rock</div>
    <div class="norm">Opera, LLC</div>
  </div>
  <div class="abs mail" style="top:3150px">
    <svg width="12" height="10" viewBox="0 0 12 10"><rect x=".6" y=".6" width="10.8" height="8.8" fill="none" stroke="#6fa85a" stroke-width="1.2"/><path d="M1 1 L6 5.5 L11 1" fill="none" stroke="#6fa85a" stroke-width="1.2"/></svg>
    info@creationrockopera.com
  </div>
  <div class="abs mail" style="top:3190px">
    <svg width="12" height="10" viewBox="0 0 12 10"><rect x=".6" y=".6" width="10.8" height="8.8" fill="none" stroke="#6fa85a" stroke-width="1.2"/><path d="M1 1 L6 5.5 L11 1" fill="none" stroke="#6fa85a" stroke-width="1.2"/></svg>
    media@creationrockopera.com
  </div>
  <div class="abs rule"></div>
  <p class="abs copyright">Copyrights © 2021 Creation The Rock Opera. All rights reserved.</p>
  <p class="abs legal">Terms of Use &nbsp;&nbsp;/&nbsp;&nbsp; Privacy Policy</p>

</div>
</body>
</html>
```